automotive repair and collision repair shop card

our company is called K.L Motor service we are a automotive repair company
we also do government inspections. the company information is on the cards. I would like you to use my new logo and create a new card and use the information from my old card. Good Luck!!

Industry/Entity Type

Car Repair

Contact Information for Business Card

Address: #417-18842 52 Ave, Surrey, BC V5K 8R3
Phone:(604) 555-0187
fax 604 555 0193
website www.klmotorworks.example

Font styles to use
Serif
Sans Serif

Requirements
Must have
• all the information
Should not have
• the owner and there name

```html
<!DOCTYPE html>
<html lang="en">
<head>
<meta charset="utf-8">
<title>K.L Motor Service – Business Card</title>
<link rel="stylesheet" href="https://fonts.googleapis.com/css2?family=Oswald:wght@300;400&family=Saira:wght@400;600;800&display=swap">
<style>
  :root {
    --page: #efe6d6;
    --card: #ffffff;
    --ink: #111111;
    --panel: #000000;
    --panel-text: #ffffff;
    --rule: #1a1a1a;
    --art-dark: #3a3a3a;
    --art-light: #d6d6d6;
  }
  * { box-sizing: border-box; margin: 0; padding: 0; }
  html, body { width: 1189px; height: 1200px; overflow: hidden; background: var(--page); }
  .canvas { position: relative; width: 1189px; height: 1200px; }

  .card {
    position: absolute; left: 171px; width: 856px; height: 488px;
    background: var(--card); border-radius: 16px; overflow: hidden;
    box-shadow: 0 4px 10px rgba(0,0,0,0.18);
  }
  .card--front { top: 67px; }
  .card--back { top: 626px; }

  .car-art {
    position: absolute; border-radius: 40px;
    background: linear-gradient(180deg, var(--art-light), var(--art-dark));
  }
  .card--front .car-art { left: 164px; top: 104px; width: 526px; height: 138px; }
  .card--back .car-art { left: 437px; top: 164px; width: 359px; height: 96px; }

  .wordmark {
    position: absolute; font-family: "Oswald", sans-serif; font-weight: 400;
    color: var(--ink); line-height: 1; white-space: nowrap; text-align: right;
    letter-spacing: 0.5px;
  }
  .tagline {
    position: absolute; font-family: "Oswald", sans-serif; font-weight: 300;
    color: var(--ink); line-height: 1; white-space: nowrap; text-align: right;
  }
  .card--front .wordmark { right: 165px; top: 251px; font-size: 62px; }
  .card--front .tagline { right: 161px; top: 322px; font-size: 24px; }

  .web-rule {
    position: absolute; left: 0; right: 0; top: 404px;
    display: flex; align-items: center; justify-content: center; gap: 16px;
  }
  .web-rule__line { width: 102px; height: 2px; background: var(--rule); }
  .web-rule__url { font-family: "Saira", sans-serif; font-weight: 800; font-size: 18px; color: var(--ink); letter-spacing: 0.5px; }

  .panel-shape { position: absolute; inset: 0; }

  .contact { position: absolute; left: 49px; top: 0; color: var(--panel-text); font-family: "Saira", sans-serif; }
  .contact__address { position: absolute; top: 204px; font-size: 21px; line-height: 27px; white-space: nowrap; letter-spacing: 0.6px; }
  .contact__list { position: absolute; top: 284px; list-style: none; }
  .contact__item { display: flex; align-items: center; height: 30px; font-size: 18px; white-space: nowrap; letter-spacing: 0.4px; }
  .contact__icon { width: 22px; height: 22px; margin-right: 14px; flex: none; }

  .card--back .wordmark { right: 56px; top: 265px; font-size: 48px; }
  .card--back .tagline { right: 56px; top: 317px; font-size: 18px; }
</style>
</head>
<body>
<main class="canvas">

  <section class="card card--front" aria-label="Card front">
    <div class="car-art" role="img" aria-label="Illustration of a dark grey sports car in side view"></div>
    <div class="wordmark">K.L MOTOR SERVICE</div>
    <div class="tagline">One Stop Repair Shop</div>
    <div class="web-rule">
      <span class="web-rule__line"></span>
      <span class="web-rule__url">www.klmotorworks.example</span>
      <span class="web-rule__line"></span>
    </div>
  </section>

  <section class="card card--back" aria-label="Card back">
    <svg class="panel-shape" width="856" height="488" viewBox="0 0 856 488" aria-hidden="true">
      <path d="M0,0 H409 C352,120 338,340 409,488 H0 Z" fill="var(--panel)"/>
      <path d="M395,0 C338,120 324,340 395,488" fill="none" stroke="#ffffff" stroke-width="2.5"/>
    </svg>

    <div class="contact">
      <div class="contact__address">#417-18842 52 Ave<br>Surrey, BC V5K 8R3</div>
      <ul class="contact__list">
        <li class="contact__item">
          <svg class="contact__icon" viewBox="0 0 22 22" aria-hidden="true"><rect width="22" height="22" rx="3" fill="#fff"/><path d="M4,9 C4,5 18,5 18,9 L15,10 L14,8 H8 L7,10 Z M6,11 H16 L17,17 H5 Z" fill="#000"/><circle cx="11" cy="14" r="1.8" fill="#fff"/></svg>
          <span>(604) 555-0187</span>
        </li>
        <li class="contact__item">
          <svg class="contact__icon" viewBox="0 0 22 22" aria-hidden="true"><rect width="22" height="22" rx="3" fill="#fff"/><rect x="7" y="4" width="8" height="5" fill="#000"/><rect x="4" y="9" width="14" height="7" rx="1" fill="#000"/><rect x="7" y="13" width="8" height="5" fill="#000" stroke="#fff" stroke-width="1"/></svg>
          <span>604 555 0193</span>
        </li>
        <li class="contact__item">
          <svg class="contact__icon" viewBox="0 0 22 22" aria-hidden="true"><rect width="22" height="22" rx="3" fill="#fff"/><rect x="4" y="6" width="14" height="10" fill="none" stroke="#000" stroke-width="1.6"/><path d="M4,6 L11,12 L18,6 M4,16 L9,11 M18,16 L13,11" fill="none" stroke="#000" stroke-width="1.4"/></svg>
          <span>info@klmotorworks.example</span>
        </li>
        <li class="contact__item">
          <svg class="contact__icon" viewBox="0 0 22 22" aria-hidden="true"><rect width="22" height="22" rx="3" fill="#fff"/><circle cx="11" cy="11" r="7" fill="none" stroke="#000" stroke-width="1.4"/><ellipse cx="11" cy="11" rx="3" ry="7" fill="none" stroke="#000" stroke-width="1.2"/><path d="M4,11 H18 M5.5,7.5 H16.5 M5.5,14.5 H16.5" stroke="#000" stroke-width="1.1"/></svg>
          <span>www.klmotorworks.example</span>
        </li>
      </ul>
    </div>

    <div class="car-art" role="img" aria-label="Illustration of a dark grey sports car in side view"></div>
    <div class="wordmark">K.L MOTOR SERVICE</div>
    <div class="tagline">One Stop Repair Shop</div>
  </section>

</main>
</body>
</html>
```